TALMORK

The business want a professional looking business card. We have a scetch we will add but want the extra upgrade, and would like more suggestions for variations of our business cards.

```html
<!DOCTYPE html>
<html lang="en">
<head>
<meta charset="utf-8">
<title>TALMORK business card</title>
<link href="https://fonts.googleapis.com/css2?family=Montserrat:wght@400;500;700&display=swap" rel="stylesheet">
<style>
  :root {
    --stage: #161616;
    --gold-light: #e9e4da;
    --gold-pale: #cdb07a;
    --gold-mid: #b48d45;
    --gold-deep: #a27932;
    --gold-dark: #7a5623;
    --name-gold: #e2b659;
    --mark-gold: #c29a4c;
    --accent-bar: #7a5416;
    --ink: #1e1b17;
  }
  * { margin: 0; padding: 0; box-sizing: border-box; }
  html, body {
    width: 1200px; height: 1059px; overflow: hidden;
    background: var(--stage);
    font-family: "Montserrat", sans-serif;
  }
  .canvas { position: relative; width: 1200px; height: 1059px; }
  .card {
    position: absolute;
    width: 690px; height: 392px;
    border-radius: 18px;
    overflow: hidden;
    background: linear-gradient(90deg, var(--gold-light) 0%, var(--gold-pale) 30%, var(--gold-mid) 56%, var(--gold-deep) 80%, var(--gold-dark) 100%);
  }
  .card--front { left: 257px; top: 89px; }
  .card--back { left: 254px; top: 547px; }

  .brand-name {
    position: absolute;
    font-weight: 500;
    color: var(--mark-gold);
    letter-spacing: 0.32em;
    white-space: nowrap;
  }
  .card--front .brand-name { left: 41px; top: 58px; font-size: 40px; }

  .decor-circle {
    position: absolute; border-radius: 50%;
    background: var(--mark-gold);
    opacity: 0.55;
  }
  .card--front .decor-circle { left: 398px; top: 53px; width: 280px; height: 280px; }

  .accent-bar {
    position: absolute; left: 0; top: 174px;
    width: 21px; height: 43px;
    background: var(--accent-bar);
  }
  .person-name {
    position: absolute; left: 41px; top: 168px;
    font-size: 24px; font-weight: 700;
    color: var(--name-gold);
  }
  .person-role {
    position: absolute; left: 42px; top: 199px;
    font-size: 19px; font-weight: 500;
    color: var(--ink);
  }
  .contact-list { position: absolute; left: 41px; top: 252px; list-style: none; }
  .contact-item {
    display: flex; align-items: center; gap: 10px;
    height: 36.5px;
    font-size: 20px; color: var(--ink);
  }
  .contact-icon { width: 15px; height: 15px; flex: none; }

  .card--back .decor-circle { left: 266px; top: 76px; width: 162px; height: 162px; opacity: 0.7; }
  .card--back .brand-name { left: 0; width: 100%; text-align: center; top: 253px; font-size: 40px; padding-left: 0.32em; }
</style>
</head>
<body>
<main class="canvas">
  <section class="card card--front">
    <div class="brand-name">TALMORK</div>
    <div class="decor-circle" role="img" aria-label="Brand emblem area"></div>
    <div class="accent-bar"></div>
    <h1 class="person-name">Anders Lie Halvorsen</h1>
    <p class="person-role">CEO &amp; Founder</p>
    <ul class="contact-list">
      <li class="contact-item">
        <svg class="contact-icon" viewBox="0 0 24 24" aria-hidden="true"><path fill="#8a6326" d="M6.6 10.8c1.4 2.8 3.8 5.1 6.6 6.6l2.2-2.2c.3-.3.7-.4 1-.2 1.1.4 2.3.6 3.6.6.6 0 1 .4 1 1V20c0 .6-.4 1-1 1C10.6 21 3 13.4 3 4c0-.6.4-1 1-1h3.5c.6 0 1 .4 1 1 0 1.3.2 2.5.6 3.6.1.3 0 .7-.2 1z"/></svg>
        <span>004755501234</span>
      </li>
      <li class="contact-item">
        <svg class="contact-icon" viewBox="0 0 24 24" aria-hidden="true"><path fill="#8a6326" d="M2 9l10-7 10 7v12H2z"/><path fill="#e9d9b4" d="M5 10l7 5 7-5V20H5z"/></svg>
        <span>talmork.llc@postmail.com</span>
      </li>
      <li class="contact-item">
        <svg class="contact-icon" viewBox="0 0 24 24" aria-hidden="true"><circle cx="12" cy="12" r="10" fill="#8a6326"/><path fill="#e9d9b4" d="M7 6c2 0 3 2 5 2s1 3-1 3-2 3-4 2-2-5 0-7zm8 7c2 0 3 2 2 4s-3 2-3 0 -1-4 1-4z"/></svg>
        <span>www.talmork.llc</span>
      </li>
    </ul>
  </section>

  <section class="card card--back">
    <div class="decor-circle" role="img" aria-label="Brand emblem area"></div>
    <div class="brand-name">TALMORK</div>
  </section>
</main>
</body>
</html>
```